Rebrand stationary with recently completed logo design

Need new business cards, thank you cards, letterhead, envelopes and presentation folders. The designs will be sent to a separate production firm so I need the files to be print ready.

My contact info
Reko Haliburn

Office 604-318-5047
Fax 604-371-8054

Email reko@glazemark.ca
website www.glazemark.ca

315-14720 62nd Avenue,
Langley, BC, V2K 3R8

Target Market(s)

Homeowners, businesses and contractors

Industry/Entity Type

Business

Font styles to use
Sans Serif

Colors
34a7d7

Requirements
Must have
• Like to have one side of the business card a solid color with the logo in all white. The side with all the text to be a white background
• I find the current blue on the front of the card with the white logo too dark.
Should not have
• Gradient colors

```html
<!DOCTYPE html>
<html lang="en">
<head>
<meta charset="utf-8">
<title>Glazemark Business Card</title>
<link href="https://fonts.googleapis.com/css2?family=Open+Sans:wght@400;600&display=swap" rel="stylesheet">
<style>
  :root {
    --brand-blue: #1a94d6;
    --slate: #3f4f5a;
    --text-grey: #555b60;
    --tag-grey: #8a8f93;
    --tag-grey-light: #9aa4ab;
    --card-white: #f7f7f7;
    --backdrop: #e4e2df;
    --white: #ffffff;
  }
  * { margin: 0; padding: 0; box-sizing: border-box; }
  html, body {
    width: 1200px; height: 960px; overflow: hidden;
    background: var(--backdrop);
    font-family: "Open Sans", Arial, sans-serif;
  }
  .card {
    position: absolute;
    width: 600px; height: 342px;
    box-shadow: 0 2px 6px rgba(0,0,0,0.25);
  }
  .card-front { left: 302px; top: 130px; background: var(--card-white); }
  .card-back { left: 299px; top: 489px; background: var(--slate); }

  .wordmark {
    position: absolute;
    font-weight: 400;
    letter-spacing: 0.5px;
    line-height: 1;
    white-space: nowrap;
  }
  .card-front .wordmark {
    left: 40px; top: 60px;
    font-size: 38px; color: var(--brand-blue);
  }
  .tagline {
    position: absolute;
    font-size: 14px; letter-spacing: 1.2px;
    color: var(--tag-grey); line-height: 1;
    white-space: nowrap;
  }
  .card-front .tagline { left: 43px; top: 100px; }

  .holder-name {
    position: absolute; left: 43px; top: 132px;
    font-size: 17px; font-weight: 600;
    color: var(--brand-blue); letter-spacing: 0.2px;
  }
  .address {
    position: absolute; left: 44px; top: 162px;
    font-size: 13px; line-height: 19px; color: var(--text-grey);
  }
  .contact-list {
    position: absolute; left: 44px; top: 210px;
    list-style: none;
    font-size: 13px; line-height: 19px; color: var(--text-grey);
  }
  .contact-list li { display: flex; align-items: center; gap: 8px; }
  .contact-list svg { width: 14px; height: 14px; fill: var(--brand-blue); }

  .front-square {
    position: absolute; left: 414px; top: 92px;
    width: 158px; height: 158px;
    background: var(--slate);
  }

  .back-lockup {
    position: absolute; left: 125px; top: 136px;
    display: flex; align-items: center; gap: 16px;
  }
  .back-square {
    width: 62px; height: 62px; background: var(--white);
  }
  .back-text { position: relative; width: 290px; height: 70px; }
  .card-back .wordmark { left: 0; top: 10px; font-size: 44px; color: var(--white); }
  .card-back .tagline { left: 4px; top: 56px; font-size: 15px; color: var(--tag-grey-light); }
</style>
</head>
<body>
  <section class="card card-front">
    <div class="wordmark">GLAZEMARK</div>
    <div class="tagline">CLEAR VIEWS, COOL ROOMS</div>
    <div class="holder-name">REKO HALIBURN</div>
    <p class="address">315-14720 62nd Avenue<br>Langley, BC, V2K 3R8</p>
    <ul class="contact-list">
      <li><svg viewBox="0 0 24 24"><path d="M6.6 10.8a15.1 15.1 0 0 0 6.6 6.6l2.2-2.2c.3-.3.7-.4 1-.2 1.1.4 2.3.6 3.6.6.6 0 1 .4 1 1V20c0 .6-.4 1-1 1A17 17 0 0 1 3 4c0-.6.4-1 1-1h3.5c.6 0 1 .4 1 1 0 1.3.2 2.5.6 3.6.1.3 0 .7-.2 1z"/></svg>604-318-5047</li>
      <li><svg viewBox="0 0 24 24"><path d="M7 3h10v5H7zM4 9h16a2 2 0 0 1 2 2v6h-4v4H6v-4H2v-6a2 2 0 0 1 2-2zm4 7v3h8v-3z"/></svg>604-371-8054</li>
      <li><svg viewBox="0 0 24 24"><path d="M2 5h20v14H2zm2 2v.5l8 5 8-5V7l-8 5z"/></svg>reko@glazemark.ca</li>
      <li><svg viewBox="0 0 24 24"><path d="M12 2a10 10 0 1 0 0 20 10 10 0 0 0 0-20zm-1 17.9A8 8 0 0 1 4.1 11H7c.1 3 .9 6 4 8.9zm2 0c3.1-2.9 3.9-5.9 4-8.9h2.9a8 8 0 0 1-6.9 8.9zM9 11h6c-.1 2.6-1 5-3 7-2-2-2.9-4.4-3-7zm0-2c.1-2.6 1-5 3-7 2 2 2.9 4.4 3 7zm-4.9 0A8 8 0 0 1 11 2.1C7.9 5 7.1 6 7 9zm12.9 0c-.1-3-.9-4-4-6.9A8 8 0 0 1 19.9 9z"/></svg>www.glazemark.ca</li>
    </ul>
    <div class="front-square" aria-hidden="true"></div>
  </section>

  <section class="card card-back">
    <div class="back-lockup">
      <div class="back-square" aria-hidden="true"></div>
      <div class="back-text">
        <div class="wordmark">GLAZEMARK</div>
        <div class="tagline">CLEAR VIEWS, COOL ROOMS</div>
      </div>
    </div>
  </section>
</body>
</html>
```